CopperWanderer Stretching and Strength

We need a application design for a our first IOS application. the goal of the application is to categorize stretching and strength routines for triathlon.

We would like to see designs that use the color orange.

The design of the application should be compliant with the last version of the IOS Mobile.

For this first design we need the folowing pages:

1- Sign up
2- Log in
3- Home
4- View Exercises
5- Do it
6- Profile

The description of each page is in the attached document.

We need a logo design for the application. The logo should express that mission of the application that is for stretch and strength training for Triathlon.

We will use https://pellavokit.example to develop the application, if you have any experience of the limitation that this technology have it will be a plus.

If you have any question please feel free to contact us.

Reason: We will extend the deadline to be sure that we select the best design from all of you. we will take the final decision next Tuesday.

Target Market(s)

The market for my aplicación is the Running a Triathlon world.

Logo Text

CopperWanderer

Font styles to use
Serif

Colors
f37122
ffffff
dcdcdc

Requirements
Must have
• In some future we will add more features in the menu. We should considere it for the design.
• The designs should include all the screens in the power point.

```html
<!DOCTYPE html>
<html lang="en">
<head>
<meta charset="utf-8">
<title>Profile</title>
<link href="https://fonts.googleapis.com/css2?family=Roboto:wght@400;500;700&display=swap" rel="stylesheet">
<style>
  :root {
    --page-bg: #d6e3ef;
    --screen-bg: #eceff2;
    --orange: #f07030;
    --white: #ffffff;
    --label: #454545;
    --value: #555a5e;
    --photo-green: #6f8f4e;
    --photo-dark: #3f5a2e;
    --photo-light: #a9bf86;
    --shirt: #9aa3a8;
  }
  * { box-sizing: border-box; margin: 0; padding: 0; }
  html, body {
    width: 1200px; height: 1200px; overflow: hidden;
    background: var(--page-bg);
    font-family: "Roboto", Arial, sans-serif;
  }
  .screen {
    position: absolute; left: 270px; top: 12px;
    width: 660px; height: 1176px;
    background: var(--screen-bg);
    overflow: hidden;
  }
  .hero-photo {
    position: absolute; left: 0; top: 0; width: 660px; height: 454px;
    background:
      radial-gradient(ellipse 40% 55% at 35% 45%, #b9a08a 0%, rgba(185,160,138,0) 70%),
      linear-gradient(180deg, rgba(0,0,0,0) 75%, var(--shirt) 75%, var(--shirt) 100%),
      radial-gradient(ellipse at 80% 30%, var(--photo-light) 0%, var(--photo-green) 45%, var(--photo-dark) 100%);
    box-shadow: 0 2px 3px rgba(0,0,0,0.15);
  }
  .status-bar {
    position: absolute; left: 0; top: 10px; width: 660px; height: 24px;
    color: var(--white); font-size: 19px; font-weight: 400;
  }
  .status-carrier { position: absolute; left: 8px; top: 0; display: flex; align-items: center; gap: 8px; }
  .status-time { position: absolute; left: 0; right: 0; text-align: center; }
  .status-right { position: absolute; right: 10px; top: 0; display: flex; align-items: center; gap: 8px; }
  .nav-bar { position: absolute; top: 58px; left: 0; width: 660px; height: 40px; }
  .menu-button { position: absolute; left: 14px; top: 6px; }
  .nav-title {
    position: absolute; left: 0; right: 0; text-align: center;
    color: var(--white); font-size: 27px; font-weight: 500; line-height: 40px;
  }
  .profile-details { position: absolute; left: 0; top: 480px; width: 660px; list-style: none; }
  .detail-row {
    display: flex; justify-content: space-between; align-items: center;
    height: 69px; padding: 0 17px 0 15px;
  }
  .detail-label { color: var(--label); font-size: 25px; font-weight: 500; }
  .detail-value { color: var(--value); font-size: 24px; font-weight: 400; }
  .edit-button {
    position: absolute; left: 44px; top: 1055px; width: 572px; height: 73px;
    border-radius: 37px; background: var(--orange);
    color: var(--white); font: 700 25px "Roboto", Arial, sans-serif;
    border: none; box-shadow: 0 3px 6px rgba(0,0,0,0.18);
  }
</style>
</head>
<body>
  <main class="screen">
    <div class="hero-photo" role="img" aria-label="Portrait photo of the user smiling outdoors in a park"></div>

    <div class="status-bar">
      <div class="status-carrier">
        <svg width="58" height="14" viewBox="0 0 58 14" aria-hidden="true">
          <g fill="#fff"><circle cx="6" cy="7" r="5"/><circle cx="18" cy="7" r="5"/><circle cx="30" cy="7" r="5"/></g>
          <g fill="none" stroke="#fff" stroke-width="1.2"><circle cx="42" cy="7" r="4.4"/><circle cx="53" cy="7" r="4.4"/></g>
        </svg>
        <span>KESTR</span>
        <svg width="20" height="16" viewBox="0 0 20 16" aria-hidden="true" fill="#fff">
          <path d="M10 15 L6.5 11 A5 5 0 0 1 13.5 11 Z"/>
          <path d="M3.5 8 A9 9 0 0 1 16.5 8 L15 9.7 A7 7 0 0 0 5 9.7 Z"/>
          <path d="M0.5 4.8 A13.5 13.5 0 0 1 19.5 4.8 L18 6.5 A11.5 11.5 0 0 0 2 6.5 Z"/>
        </svg>
      </div>
      <div class="status-time">4:21 PM</div>
      <div class="status-right">
        <svg width="12" height="20" viewBox="0 0 12 20" aria-hidden="true">
          <path d="M1 5 L10 14 L5.5 18.5 V1.5 L10 6 L1 15" fill="none" stroke="#fff" stroke-width="1.4"/>
        </svg>
        <span>100%</span>
        <svg width="40" height="18" viewBox="0 0 40 18" aria-hidden="true">
          <rect x="1" y="2" width="34" height="14" rx="3" fill="none" stroke="#fff" stroke-width="1.4"/>
          <rect x="3" y="4" width="30" height="10" rx="1.5" fill="#fff"/>
          <rect x="36.5" y="6.5" width="2.5" height="5" rx="1" fill="#fff"/>
        </svg>
      </div>
    </div>

    <header class="nav-bar">
      <svg class="menu-button" width="32" height="24" viewBox="0 0 32 24" aria-label="Menu" role="img">
        <g stroke="#fff" stroke-width="3"><line x1="1" y1="3" x2="31" y2="3"/><line x1="1" y1="12" x2="31" y2="12"/><line x1="1" y1="21" x2="31" y2="21"/></g>
      </svg>
      <h1 class="nav-title">PROFILE</h1>
    </header>

    <ul class="profile-details">
      <li class="detail-row"><span class="detail-label">Full Name</span><span class="detail-value">Reno Castell</span></li>
      <li class="detail-row"><span class="detail-label">Username</span><span class="detail-value">renocastell98</span></li>
      <li class="detail-row"><span class="detail-label">Age</span><span class="detail-value">25</span></li>
      <li class="detail-row"><span class="detail-label">Gender</span><span class="detail-value">Male</span></li>
      <li class="detail-row"><span class="detail-label">Email Id</span><span class="detail-value">renocastell98@mailbox.example</span></li>
      <li class="detail-row"><span class="detail-label">City</span><span class="detail-value">Alderton, US</span></li>
      <li class="detail-row"><span class="detail-label">Sports</span><span class="detail-value">Bike and Running</span></li>
    </ul>

    <button class="edit-button" type="button">EDIT PROFILE</button>
  </main>
</body>
</html>
```